Web Design for a Biotech Consulting Firm

We need a web site design for a new business based in Philadelphia called Verantel Dx. This is a consulting firm that will serve medical diagnostics industry, which is part of the life science/healthcare industry focusing on developing and marketing products that help in early detection, monitoring or management of diseases. Our consulting firm will help medical diagnostic companies to overcome key challenges in designing, evaluating and marketing new products.Our company name is Verantel Dx. Verantel is Latin word for "something" Dx represents diagnostics. The idea behind the name is that we help companies to transform the original, early product ideas ("nothing") into "something"; which is a product with full clinical utility that will help to improve health and well-being.The web site should use the visual feel of the logo (attached), be modern, simple and clean looking and represent creativity, innovation, scientific thinking and progress.
Updates

Wix Design is acceptable

Industry/Entity Type

Biotechnology

Coding

Coded - Design and coding required

Number of Pages Required

1 page

Font styles to use
Sans Serif

Requirements
Must have
• simple, clean look couple of pages
Should not have
• a lot of pages

```html
<!DOCTYPE html>
<html lang="en">
<head>
<meta charset="utf-8">
<title>Verantel Dx — Biotech Consulting Firm</title>
<link href="https://fonts.googleapis.com/css2?family=Urbanist:wght@400;500;600;700&display=swap" rel="stylesheet">
<style>
:root{
  --blue:#1f74d9;
  --ink:#1b1e24;
  --text:#4a4f57;
  --muted:#8a9099;
  --pale:#e8f0fa;
  --line:#e3e7ec;
  --footer:#173f55;
  --white:#fff;
}
*{box-sizing:border-box;margin:0;padding:0}
html,body{width:1200px;height:2989px;overflow:hidden}
body{position:relative;font-family:"Urbanist",sans-serif;color:var(--ink);background:var(--white)}
.abs{position:absolute}
a{color:inherit;text-decoration:none}

/* hero */
.hero{left:0;top:0;width:1200px;height:706px}
.hero-photo{position:absolute;inset:0;clip-path:polygon(0 0,100% 0,100% 607px,0 706px);
  background:radial-gradient(circle at 70% 20%,#8a2a45 0,transparent 28%),
  radial-gradient(circle at 90% 50%,#5e1f3c 0,transparent 25%),
  linear-gradient(160deg,#2c5f9c 0%,#3b6fae 40%,#2d5590 70%,#1f3d72 100%)}
.logo{left:142px;top:23px;width:95px;height:93px;border:2px solid var(--blue);border-right:none}
.logo::after{content:"";position:absolute;right:0;top:0;width:2px;height:20px;background:var(--blue)}
.logo-text{left:155px;top:56px;font-size:22px;font-weight:500;color:var(--white);white-space:nowrap}
.logo-text span{color:var(--blue)}
.nav{left:505px;top:52px;display:flex;align-items:center;gap:0}
.nav a{font-size:16px;color:var(--white);height:35px;line-height:35px;padding:0 19px;margin-right:11px}
.nav a.active{background:var(--blue);width:84px;text-align:center;padding:0}
.hero-title{left:0;width:1200px;top:238px;text-align:center;font-size:56px;font-weight:700;color:var(--white);text-shadow:0 2px 6px rgba(0,0,0,.25)}
.hero-sub{left:300px;width:600px;top:318px;text-align:center;font-size:19px;line-height:26px;color:var(--white)}
.btn{display:block;background:var(--blue);color:var(--white);font-size:15px;text-align:center}
.hero-btn{left:550px;top:408px;width:128px;height:35px;line-height:35px}

/* about */
.about{left:0;top:600px;width:1200px;height:672px;background:var(--pale);z-index:-1}
.about-frame{left:142px;top:791px;width:418px;height:406px;border:3px solid var(--blue)}
.about-photo{left:190px;top:755px;width:409px;height:403px;background:linear-gradient(135deg,#dfeef8 0%,#7fb6dc 45%,#2e7fc0 75%,#1a4e86 100%)}
.heading{font-size:28px;font-weight:500;white-space:nowrap}
.heading span{color:var(--blue)}
.bracket{width:62px;border:2px solid var(--blue);border-right:none}
.bracket::after{content:"";position:absolute;right:0;top:0;width:2px;height:14px;background:var(--blue)}
.bracket::before{content:"";position:absolute;right:0;bottom:0;width:2px;height:14px;background:var(--blue)}
.about-text{left:643px;top:906px;width:420px;font-size:14.5px;line-height:25.5px;color:var(--ink)}
.about-btn{left:643px;top:1071px;width:130px;height:37px;line-height:37px}

/* services */
.card{border:2px solid var(--line);background:var(--white);text-align:center}
.svc{top:1451px;width:218px;height:260px}
.svc-icon{position:absolute;left:73px;top:44px;width:70px;height:70px;border:2px solid #9fb8d8;display:flex;align-items:center;justify-content:center}
.svc h3{position:absolute;left:0;width:100%;top:135px;font-size:17px;font-weight:600}
.svc p{position:absolute;left:12px;right:12px;top:164px;font-size:12.5px;line-height:18px;color:var(--muted)}

/* reviews */
.reviews{left:0;top:1782px;width:1200px;height:479px;background:linear-gradient(120deg,#dbe6f2 0%,#c6d7ea 50%,#d6e3f0 100%)}
.review{top:2005px;width:294px;height:186px;background:#f8fafc;border:none}
.review p{position:absolute;left:16px;right:16px;top:56px;font-size:13.5px;line-height:19px;color:var(--text)}
.review .name{position:absolute;left:0;width:100%;top:146px;font-size:16px;color:var(--blue);font-weight:600}
.avatar{top:1968px;width:81px;height:81px;border:2px solid var(--blue);background:linear-gradient(180deg,#c9d6e4,#2d3d58)}
.arrow{width:23px;height:23px;border:1.5px solid var(--muted);display:flex;align-items:center;justify-content:center}
.arrow.next{border-color:var(--blue)}

/* partners */
.partner{top:2449px;width:210px;height:120px;border:none;box-shadow:0 2px 10px rgba(20,40,70,.08);display:flex;align-items:center;justify-content:center;gap:10px;font-size:22px;font-weight:600;color:var(--ink)}
.partner i{display:block;width:30px;height:30px;border-radius:50%;background:var(--blue)}

/* footer */
.footer{left:0;top:2650px;width:1200px;height:339px;background:var(--footer);color:var(--white)}
.f-logo{left:143px;top:2714px;width:77px;height:77px;border:2px solid var(--blue);border-right:none}
.f-logo::after{content:"";position:absolute;right:0;top:0;width:2px;height:16px;background:var(--blue)}
.f-logo-text{left:154px;top:2741px;font-size:19px;color:var(--white);white-space:nowrap}
.f-logo-text span{color:var(--blue)}
.f-about{left:142px;top:2802px;width:200px;font-size:12.5px;line-height:19px}
.f-head{top:2712px;font-size:17px;font-weight:600;color:var(--blue)}
.f-links{left:453px;top:2750px;list-style:none;font-size:13px;line-height:25.8px}
.f-info{left:670px;top:2752px;list-style:none;font-size:13px;line-height:19px}
.f-info li,.f-social li{display:flex;gap:10px;align-items:flex-start;margin-bottom:17px}
.f-social{left:966px;top:2752px;list-style:none;font-size:13px}
.f-social li{margin-bottom:12px;align-items:center}
.dot{width:10px;height:10px;border-radius:50%;background:var(--white);flex:none}
.f-rule{left:142px;top:2894px;width:916px;height:1px;background:rgba(255,255,255,.15)}
.copy{left:0;width:1200px;top:2922px;text-align:center;font-size:11.5px;color:#c9d5de}
.copy b{color:var(--white);font-weight:600}
</style>
</head>
<body>

<section class="hero abs">
  <div class="hero-photo" role="img" aria-label="Close-up of molecules, blood cells and virus particles in blue and red tones"></div>
</section>
<div class="logo abs"></div>
<div class="logo-text abs">Verantel <span>Dx</span></div>
<nav class="nav abs">
  <a class="active" href="#">Home</a><a href="#">About Us</a><a href="#">Services</a><a href="#">Innovations</a><a href="#">Contact Us</a>
</nav>
<h1 class="hero-title abs">Biotech Consulting Firm</h1>
<p class="hero-sub abs">We Will Serve Medical Diagnostics Industry, Which Is Part Of The Life Science/healthcare Industry.</p>
<a class="btn hero-btn abs" href="#">Read More</a>

<div class="about abs"></div>
<div class="about-frame abs"></div>
<div class="about-photo abs" role="img" aria-label="Laboratory glassware with a gloved hand holding a flask of blue liquid"></div>
<div class="bracket abs" style="left:643px;top:812px;height:64px"></div>
<h2 class="heading abs" style="left:669px;top:827px">About <span>Verantel Dx</span></h2>
<p class="about-text abs">We are a Biotech consulting firm and we will serve medical diagnostics industry, which is part of the life science/healthcare industry focusing on developing and marketing products that help in early detection, monitoring or management of diseases.</p>
<a class="btn about-btn abs" href="#">Read More</a>

<div class="bracket abs" style="left:506px;top:1343px;height:64px"></div>
<h2 class="heading abs" style="left:530px;top:1356px">Our <span>Services</span></h2>

<div class="card svc abs" style="left:142px">
  <div class="svc-icon"><svg width="38" height="38" viewBox="0 0 38 38" fill="none" stroke="#1b1e24" stroke-width="1.6"><rect x="4" y="6" width="30" height="22" rx="3"/><circle cx="14" cy="15" r="3"/><path d="M10 28v6M16 28v6M24 12l4 4-4 4"/></svg></div>
  <h3>Corporate Strategy</h3>
  <p>Lorem Ipsum is simply dummy text of the printing and typesetting industry.</p>
</div>
<div class="card svc abs" style="left:374px">
  <div class="svc-icon"><svg width="38" height="38" viewBox="0 0 38 38" fill="none" stroke="#1b1e24" stroke-width="1.6"><path d="M6 6h14l6 6v20H6z"/><path d="M10 16h12M10 21h8M10 26h6"/><circle cx="27" cy="27" r="5"/></svg></div>
  <h3>Product Development</h3>
  <p>Lorem Ipsum is simply dummy text of the printing and typesetting industry.</p>
</div>
<div class="card svc abs" style="left:606px">
  <div class="svc-icon"><svg width="38" height="38" viewBox="0 0 38 38" fill="none" stroke="#1b1e24" stroke-width="1.6"><circle cx="19" cy="9" r="6"/><path d="M19 6v6"/><path d="M3 22l7-4 8 4 6-3 11 4M10 18l9 10 6-4"/></svg></div>
  <h3>Business Development</h3>
  <p>Lorem Ipsum is simply dummy text of the printing and typesetting industry.</p>
</div>
<div class="card svc abs" style="left:840px">
  <div class="svc-icon"><svg width="38" height="38" viewBox="0 0 38 38" fill="none" stroke="#1b1e24" stroke-width="1.6"><rect x="16" y="5" width="17" height="17"/><path d="M16 11h17M16 16h17M22 5v17M27 5v17"/><circle cx="11" cy="17" r="5"/><path d="M8 24v9h8"/></svg></div>
  <h3>Commercialization</h3>
  <p>Lorem Ipsum is simply dummy text of the printing and typesetting industry.</p>
</div>

<section class="reviews abs" role="img" aria-label="Soft medical background with faint lab icons"></section>
<div class="bracket abs" style="left:469px;top:1853px;height:64px"></div>
<h2 class="heading abs" style="left:493px;top:1866px">Customer <span>Reviews</span></h2>

<div class="arrow abs" style="left:81px;top:2084px"><svg width="10" height="12" viewBox="0 0 10 12" fill="none" stroke="#8a9099" stroke-width="1.5"><path d="M7 1L2 6l5 5"/></svg></div>
<div class="arrow next abs" style="left:1094px;top:2084px"><svg width="10" height="12" viewBox="0 0 10 12" fill="none" stroke="#1f74d9" stroke-width="1.5"><path d="M3 1l5 5-5 5"/></svg></div>

<div class="card review abs" style="left:142px"><p>Lorem ipsum dolor sit amet, consectetuer adipiscing elit, sed diam nonummy nibh euismod tincidunt ut laoreet dolore magna aliquam erat volutpat.</p><div class="name">Mara</div></div>
<div class="card review abs" style="left:453px"><p>Lorem ipsum dolor sit amet, consectetuer adipiscing elit, sed diam nonummy nibh euismod tincidunt ut laoreet dolore magna aliquam erat volutpat.</p><div class="name">Mara</div></div>
<div class="card review abs" style="left:765px"><p>Lorem ipsum dolor sit amet, consectetuer adipiscing elit, sed diam nonummy nibh euismod tincidunt ut laoreet dolore magna aliquam erat volutpat.</p><div class="name">Mara</div></div>
<div class="avatar abs" style="left:248px" role="img" aria-label="Customer portrait"></div>
<div class="avatar abs" style="left:559px" role="img" aria-label="Customer portrait"></div>
<div class="avatar abs" style="left:871px" role="img" aria-label="Customer portrait"></div>

<div class="bracket abs" style="left:502px;top:2332px;height:64px"></div>
<h2 class="heading abs" style="left:526px;top:2345px">Our <span>Partners</span></h2>

<div class="arrow abs" style="left:81px;top:2511px"><svg width="10" height="12" viewBox="0 0 10 12" fill="none" stroke="#8a9099" stroke-width="1.5"><path d="M7 1L2 6l5 5"/></svg></div>
<div class="arrow next abs" style="left:1094px;top:2511px"><svg width="10" height="12" viewBox="0 0 10 12" fill="none" stroke="#1f74d9" stroke-width="1.5"><path d="M3 1l5 5-5 5"/></svg></div>
<div class="card partner abs" style="left:142px">Northfield<i></i></div>
<div class="card partner abs" style="left:377px"><i></i>Corvane</div>
<div class="card partner abs" style="left:612px">Helixa<i></i></div>
<div class="card partner abs" style="left:847px"><i></i>Tessaro</div>

<footer class="footer abs" role="img" aria-label="Dark teal background with faint cell texture"></footer>
<div class="f-logo abs"></div>
<div class="f-logo-text abs">Verantel <span>Dx</span></div>
<p class="f-about abs">Lorem ipsum dolor sit amet, consectetuer adipiscing elit, sed diam.</p>

<h4 class="f-head abs" style="left:453px">Quick Links</h4>
<ul class="f-links abs"><li>Home</li><li>About Us</li><li>Services</li><li>Innovations</li><li>Contact Us</li></ul>

<h4 class="f-head abs" style="left:670px">Our Information</h4>
<ul class="f-info abs">
  <li><svg width="12" height="16" viewBox="0 0 12 16"><path d="M6 0a6 6 0 0 0-6 6c0 4.5 6 10 6 10s6-5.5 6-10a6 6 0 0 0-6-6zm0 8.5A2.5 2.5 0 1 1 6 3.5a2.5 2.5 0 0 1 0 5z" fill="#fff"/></svg><span>11223 Lorem ipsum dolar<br>met ulorem, 3344</span></li>
  <li><svg width="14" height="14" viewBox="0 0 14 14"><path d="M3 0l3 3-2 2c1 2 3 4 5 5l2-2 3 3-2 3C6 13 1 8 0 2z" fill="#fff"/></svg><span>+11 555 010 234</span></li>
  <li><svg width="15" height="11" viewBox="0 0 15 11"><rect width="15" height="11" rx="1" fill="#fff"/><path d="M0 1l7.5 5L15 1" fill="none" stroke="#173f55" stroke-width="1.4"/></svg><span>info@verantel-dx.com</span></li>
</ul>

<h4 class="f-head abs" style="left:966px">Follow Us</h4>
<ul class="f-social abs"><li><span class="dot"></span>Friendly</li><li><span class="dot"></span>Chirper</li></ul>

<div class="f-rule abs"></div>
<p class="copy abs">© 2019 <b>Verantel Dx.</b> All rights reserved.</p>

</body>
</html>
```